Brightway Haus Inc. Business Card Design

Brightway Haus Inc. is in search of a great clean design for our business cards!

Looking to incorporate our full logo and watermark on side one (however, I am open to having the text and watermark separated within the design.)

On side two, I am looking to have contact information (Name, Position, Phone #, Email, Website (www.thebrightwayhaus.ca). Can have the logo and/or watermark as part of the design if applicable.

Please add tagline "Where Shine Counts" on either side 1 or 2. This tagline can be in a sans serif, serif or cursive font as long as it compliments overall design. Capitalization can be title or sentence case depending on how it fits within the design.

Get creative!! Looking for a clean, crisp, premium design! Looking for a glossy card finish with spot UV features when printed. Cards will also be printed with rounded corners. Standard dimensions (3.5 x 2).

Target Market(s)

B2B - primary clients are business owners or property management corporations. (residential jobs are few and far between)

Industry/Entity Type

Business

Contact Information for Business Card

- clean, crisp design
- double sided
- spot UV accents and glossy finish upon printing
- standard business card size (3.5 x 2) with rounded corners
- please see project description for requirements per side

Font styles to use
Sans Serif

Requirements
Must have
• - adequate bleeds with print ready files
• - cohesive design elements between side 1 & 2
• - spot UV elements (can be on both sides or just one, use your discretion)
• - colour pallet should match the logo file provided
• - incorporate tagline "where shine counts" (this tagline can be in a serif or sans serif font as long as it is complimentary to the overall design.
Nice to have
• - Premium elements with a clean design
Should not have
• - Please omit cartoon or whimsical like designs, think premium.
• - Colours should not stray from the pallet of the provided logo.

```html
<!DOCTYPE html>
<html lang="en">
<head>
<meta charset="utf-8">
<title>Brightway Haus Inc. Business Cards</title>
<link href="https://fonts.googleapis.com/css2?family=Open+Sans:wght@400;600;700&family=Roboto+Condensed:wght@400;700&display=swap" rel="stylesheet">
<style>
  :root {
    --backdrop: #2b2b2b;
    --teal: #12b8bb;
    --teal-deep: #0fa9ac;
    --navy: #1b2556;
    --paper: #f2f2f2;
    --white: #ffffff;
    --grey: #a9a9a9;
  }
  * { margin: 0; padding: 0; box-sizing: border-box; }
  html, body {
    width: 1200px; height: 960px; overflow: hidden;
    background: var(--backdrop);
    font-family: "Open Sans", Arial, sans-serif;
  }
  .canvas { position: relative; width: 1200px; height: 960px; }

  .card {
    position: absolute; left: 320px; width: 600px;
    border-radius: 18px; overflow: hidden;
  }

  /* Side one */
  .card--front { top: 105px; height: 345px; background: var(--teal); }
  .front-brand {
    position: absolute; right: 36px; bottom: 36px; text-align: left;
    color: var(--white);
  }
  .front-brand__name {
    font-family: "Roboto Condensed", Arial, sans-serif;
    font-weight: 700; font-size: 31px; line-height: 1; letter-spacing: -0.3px;
  }
  .front-brand__tagline {
    margin-top: 6px; font-size: 14px; letter-spacing: 2.2px; font-weight: 400;
  }

  /* Side two */
  .card--back { top: 493px; height: 342px; background: var(--paper); }
  .back-brand {
    position: absolute; top: 72px; left: 0; width: 100%;
    display: flex; justify-content: center; align-items: center; gap: 12px;
  }
  .back-brand__mark { width: 34px; height: 34px; background: var(--teal); }
  .back-brand__name {
    font-family: "Roboto Condensed", Arial, sans-serif;
    font-weight: 700; font-size: 46px; line-height: 1; color: var(--navy);
    letter-spacing: -0.5px;
  }
  .person {
    position: absolute; top: 168px; left: 0; width: 100%;
    display: flex; justify-content: center; align-items: center;
  }
  .person__name {
    font-family: "Roboto Condensed", Arial, sans-serif;
    font-weight: 700; font-size: 22px; color: var(--teal);
  }
  .person__divider { width: 1px; height: 18px; background: var(--navy); margin: 0 6px 0 8px; }
  .person__role {
    font-family: "Roboto Condensed", Arial, sans-serif;
    font-size: 16px; color: var(--navy);
  }

  .contact-band {
    position: absolute; top: 245px; left: 0; width: 100%; height: 63px;
    background: var(--navy); color: var(--white);
    display: flex; align-items: center; font-size: 14px; line-height: 20px;
  }
  .contact-band__group { padding: 0 18px; }
  .contact-band__group--address { padding-left: 33px; }
  .contact-band__rule { width: 1px; height: 40px; background: rgba(255,255,255,0.55); }
  .contact-line { display: flex; align-items: center; gap: 8px; white-space: nowrap; }
  .contact-line svg { width: 13px; height: 13px; fill: var(--teal); flex: none; }
</style>
</head>
<body>
<div class="canvas">

  <section class="card card--front" aria-label="Card side one">
    <div class="front-brand">
      <div class="front-brand__name">BRIGHTWAY HAUS INC.</div>
      <div class="front-brand__tagline">Where Shine Counts</div>
    </div>
  </section>

  <section class="card card--back" aria-label="Card side two">
    <div class="back-brand">
      <span class="back-brand__mark"></span>
      <span class="back-brand__name">BRIGHTWAY HAUS INC.</span>
    </div>

    <div class="person">
      <span class="person__name">DANIEL MERCER</span>
      <span class="person__divider"></span>
      <span class="person__role">CEO/FOUNDER</span>
    </div>

    <div class="contact-band">
      <div class="contact-band__group contact-band__group--address">
        <div>4120 Harbor View Road</div>
        <div>Juneau, Alaska 99801</div>
      </div>
      <span class="contact-band__rule"></span>
      <div class="contact-band__group">
        <div class="contact-line">
          <svg viewBox="0 0 24 24" aria-hidden="true"><path d="M6.6 10.8c1.4 2.8 3.8 5.1 6.6 6.6l2.2-2.2c.3-.3.7-.4 1-.2 1.1.4 2.3.6 3.6.6.6 0 1 .4 1 1V20c0 .6-.4 1-1 1C10.6 21 3 13.4 3 4c0-.6.4-1 1-1h3.5c.6 0 1 .4 1 1 0 1.3.2 2.5.6 3.6.1.3 0 .7-.2 1z"/></svg>
          907 555 0148
        </div>
        <div class="contact-line">
          <svg viewBox="0 0 24 24" aria-hidden="true"><path d="M7 1h10c1.1 0 2 .9 2 2v18c0 1.1-.9 2-2 2H7c-1.1 0-2-.9-2-2V3c0-1.1.9-2 2-2zm0 3v14h10V4z"/></svg>
          907 555 0162
        </div>
      </div>
      <span class="contact-band__rule"></span>
      <div class="contact-band__group">
        <div class="contact-line">
          <svg viewBox="0 0 24 24" aria-hidden="true"><path d="M6 2h12v5H6zM4 8h16c1.1 0 2 .9 2 2v7h-4v5H6v-5H2v-7c0-1.1.9-2 2-2zm4 8v4h8v-4z"/></svg>
          907 555 0175
        </div>
        <div class="contact-line">
          <svg viewBox="0 0 24 24" aria-hidden="true"><path d="M2 5h20v14H2zm2 2v.5l8 5 8-5V7z"/></svg>
          hello@thebrightwayhaus.ca
        </div>
      </div>
    </div>
  </section>

</div>
</body>
</html>
```